Local Chiropractor Needs Up Scale Webdesign

This website needs to have an upscale look with a very modern feel. Below is the information and websites to reference

Add Logo that is attached

Build a color scheme similar to this website image titled "chiro-1"

Must Include these pages in a horizontal menu bar in this order:
Home, Meet Our Staff, Patient Testimonials, Videos, Work Place Wellness, Contact

Build a "classy looking" Make An Appointment Button into the header with the contact info below

Phone Number:
555-314-2719

Address:
3168 Pelham Orchard Lane, #240
Maple Hollow, MN 55999

This website needs 4 rotating banners. Please reference a layout similar to this for the banners: http://drmorlatz.example/. However design it nicer than this website, this website is very boring and doesn't flow with the colors properly

Below are the description for each banner

Rotating Banner #1
Use Image: Pediatrics
Two lines of text. First line title line, second description. Use Latin text for fill

Rotating Banner #2
Use Image: Aging Gracefully

Rotating Banner #3
Use Image: Pregnancy

Rotating Banner #4
Use Image: Athletics

I'd like to see a free consultation box similar to the "chiro-1" image. Fields to include are: First Name, Last Name, Phone Number, Comments.

For the body, please fill it with latin text. Please design a professional body layout. You can include a box in the right column for the hours

Office Hours
Monday: 8:00-11:00, 2:00-5:00
Tuesday: 8:30-11:00, 2:00-5:30
Wednesday: 8:00-11:00, 2:00-5:00
Thursday: 10:00-12:00, 2:30-5:00
Friday: 8:00-10:00, 1:00-5:00
Saturday: Closed
Sunday: Closed

For the footer please design something similar to the: http://drmorlatz.example/

Also include in the Footer: Powered by Brightline Site Works

```html
<!DOCTYPE html>
<html lang="en">
<head>
<meta charset="utf-8">
<title>Evergreen Vitality Chiropractic</title>
<link href="https://fonts.googleapis.com/css2?family=Dosis:wght@400;500;600&family=Open+Sans:ital,wght@0,400;0,600;0,700;1,400&display=swap" rel="stylesheet">
<style>
:root{
  --charcoal:#474747;
  --card:#4f4f4f;
  --lime:#c8dc3a;
  --lime-dark:#8f9c22;
  --green:#7cb82f;
  --orange:#d4532a;
  --cyan:#25c4cc;
  --black:#0d0d0d;
  --white:#ffffff;
  --text:#3c3c3c;
}
*{margin:0;padding:0;box-sizing:border-box}
html,body{width:821px;height:1200px;overflow:hidden;background:var(--white)}
body{position:relative;font-family:"Open Sans",sans-serif;color:var(--text)}
.abs{position:absolute}
.condensed{font-family:"Dosis",sans-serif}

.site-header{left:0;top:0;width:821px;height:74px;background:var(--charcoal);color:var(--white)}
.header-contact{left:86px;top:18px;font-family:"Dosis",sans-serif;font-size:11px;line-height:13px}
.header-contact .row{display:flex;gap:6px;align-items:flex-start;margin-bottom:6px}
.brand{left:330px;top:22px;width:170px;display:flex;align-items:center;gap:8px}
.brand-dot{width:18px;height:18px;border-radius:50%;background:var(--lime);flex:none}
.brand-name{font-family:"Dosis",sans-serif;font-weight:600;font-size:15px;line-height:16px;color:var(--lime)}
.appt-btn{left:621px;top:16px;width:115px;height:42px;background:var(--lime);border-left:4px solid var(--lime-dark);color:#333;font-family:"Dosis",sans-serif;font-weight:600;font-size:12px;text-align:center;padding-top:4px}

.main-nav{left:0;top:74px;width:821px;height:29px;background:var(--lime);display:flex;padding-left:85px}
.main-nav a{display:block;height:29px;line-height:29px;font-family:"Dosis",sans-serif;font-size:11px;color:#333;text-decoration:none;text-align:center;border-left:1px solid #b3c52f}
.main-nav a:last-child{border-right:1px solid #b3c52f}

.hero{left:0;top:103px;width:821px;height:355px;background:linear-gradient(90deg,#5b4a2a 0%,#7f8a3c 30%,#a7a762 55%,#6e7a3a 80%,#4a3d24 100%)}
.hero-caption{left:68px;top:236px;width:444px;height:112px;background:rgba(200,220,58,.82);padding:8px 18px}
.hero-caption h1{font-family:"Open Sans",sans-serif;font-weight:700;font-size:23.5px;color:#3a3a3a;line-height:27px;white-space:nowrap}
.hero-caption p{font-size:10.5px;line-height:13px;color:#4a4a2a;margin-top:3px;width:370px}
.hero-btn{display:inline-block;margin-top:9px;background:var(--charcoal);color:#fff;font-size:10.5px;padding:5px 9px}
.hero-arrow{top:269px;width:23px;height:22px;background:#333;color:#fff;font-size:11px;text-align:center;line-height:22px}

.welcome{left:86px;top:474px;width:360px}
.welcome h2{font-weight:600;font-size:17px;color:var(--green)}
.welcome p{font-size:8.8px;line-height:14px;color:#333}

.service{width:205px;height:113px;background:var(--card);color:#fff;text-align:center}
.service .icon{position:absolute;left:80px;top:-24px;width:46px;height:46px;border-radius:50%;background:var(--lime)}
.service h3{font-weight:600;font-size:12.5px;padding-top:25px;line-height:17px}
.service p{font-size:8.6px;line-height:11.7px;padding:2px 7px 0;text-align:justify;text-align-last:center}
.service .more{position:absolute;left:0;bottom:0;width:205px;height:20px;background:var(--lime);color:#444;font-weight:600;font-size:11.5px;line-height:20px}

.testimonial{left:85px;top:848px;width:428px;height:107px;background:var(--card);color:#fff;text-align:center}
.testimonial h3{font-weight:600;font-size:12.5px;padding-top:5px}
.testimonial blockquote{font-style:italic;font-size:9.4px;line-height:15px;padding:6px 8px 0}
.testimonial cite{position:absolute;left:360px;top:70px;color:var(--lime);font-size:9.5px;line-height:12px;font-style:italic}
.dots{position:absolute;left:197px;top:94px;display:flex;gap:3px}
.dots span{width:6px;height:6px;border-radius:50%;background:#fff}

.consult{left:531px;top:484px;width:206px;height:225px}
.consult-body{position:absolute;left:0;top:0;width:206px;height:225px;background:var(--lime)}
.field{position:absolute;left:22px;width:160px;height:17px;background:#fff;font-size:7px;color:#888;padding:4px 6px}
.submit{position:absolute;left:22px;top:196px;width:160px;height:17px;background:var(--lime-dark);color:#fff;font-size:9px;font-weight:700;text-align:center;line-height:17px;letter-spacing:.5px}

.hours{left:531px;top:746px;width:206px;height:206px;background:var(--charcoal);padding:0 5px}
.hours h3{font-family:"Dosis",sans-serif;font-weight:500;font-size:14px;color:#fff;text-align:center;height:25px;line-height:28px}
.hours table{width:196px;border-collapse:collapse;background:var(--lime)}
.hours td{height:24.7px;font-size:9.5px;font-weight:600;color:#444;border-bottom:1px solid #b3c52f;padding-left:8px}

.site-footer{left:0;top:968px;width:821px;height:232px;background:var(--black);color:#fff;font-family:"Dosis",sans-serif}
.band{top:2px;height:36px;font-size:18px;text-align:center;line-height:36px;color:#fff}
.f-title{font-size:13px;text-decoration:underline;text-underline-offset:3px}
.f-row{display:flex;gap:10px;align-items:center;font-size:10px;line-height:15px}
.map{left:283px;top:62px;width:187px;height:109px;border:2px solid var(--lime);background:linear-gradient(135deg,#d9e3c8,#b9d3e6 60%,#dbe4cf)}
.f-hours td{font-size:8px;height:17.6px;border-bottom:1px solid #fff;padding-right:4px}
.powered{left:86px;top:212px;font-size:9px;color:#aaa}
</style>
</head>
<body>

<header class="abs site-header">
  <div class="abs header-contact">
    <div class="row">
      <svg width="9" height="12" viewBox="0 0 9 12"><path d="M4.5 0A4.5 4.5 0 0 0 0 4.5C0 8 4.5 12 4.5 12S9 8 9 4.5A4.5 4.5 0 0 0 4.5 0z" fill="#ddd"/><circle cx="4.5" cy="4.5" r="1.6" fill="#474747"/></svg>
      <span>3168 Pelham Orchard Lane, #240<br>Maple Hollow, MN 55999</span>
    </div>
    <div class="row">
      <svg width="11" height="11" viewBox="0 0 11 11"><circle cx="5.5" cy="5.5" r="5" fill="none" stroke="#ddd"/><path d="M3.5 3l1 1-0.5 1c.5 1 1 1.5 2 2l1-.5 1 1-1 1C5 8 3 6 2.8 4z" fill="#ddd"/></svg>
      <span>555-314-2719</span>
    </div>
  </div>
  <div class="abs brand">
    <span class="brand-dot"></span>
    <span class="brand-name">Evergreen Vitality Chiropractic</span>
  </div>
  <a class="abs appt-btn">
    <svg width="18" height="16" viewBox="0 0 18 16"><rect x="1" y="2" width="16" height="13" rx="2" fill="none" stroke="#333" stroke-width="1.5"/><line x1="1" y1="5" x2="17" y2="5" stroke="#333"/><path d="M5 9.5l3 2.5 5-5" fill="none" stroke="#333" stroke-width="1.6"/></svg><br>Make An Appointment
  </a>
</header>

<nav class="abs main-nav">
  <a style="width:78px">Home</a>
  <a style="width:117px">Meet Our Staff</a>
  <a style="width:138px">Patient Testimonials</a>
  <a style="width:84px">Videos</a>
  <a style="width:141px">Work Place Wellness</a>
  <a style="width:93px">Contact</a>
</nav>

<section class="abs hero" role="img" aria-label="Photo of two smiling older women jogging on a forest path with water bottles"></section>
<div class="abs hero-caption">
  <h1>The standard Lorem Ipsum passage</h1>
  <p>Sed ut perspiciatis unde omnis iste natus error sit voluptatem accusantium doloremque laudantium, totam rem tore veritatis</p>
  <span class="hero-btn">Know More</span>
</div>
<div class="abs hero-arrow" style="left:0">&laquo;</div>
<div class="abs hero-arrow" style="left:798px">&raquo;</div>

<section class="abs welcome">
  <h2>Welcome To Evergreen Vitality</h2>
  <p>There are many variations of passages of Lorem Ipsum available, but the majority have suffered alteration in some form, by injected humour, or randomised words which don't look even slightly believable. If you</p>
</section>

<article class="abs service" style="left:85px;top:570px"><span class="icon"></span><h3>Pediatrics</h3><p>There are many variations of passages of Lorem Ipsum available, but the majority variations of passages of have suffered alteration in some form</p><div class="more">Read More</div></article>
<article class="abs service" style="left:308px;top:570px"><span class="icon"></span><h3>Aging Gracefully</h3><p>There are many variations of passages of Lorem Ipsum available, but the majority variations of passages of have suffered alteration in some form</p><div class="more">Read More</div></article>
<article class="abs service" style="left:85px;top:716px"><span class="icon"></span><h3>Pregnancy</h3><p>There are many variations of passages of Lorem Ipsum available, but the majority variations of passages of have suffered alteration in some form</p><div class="more">Read More</div></article>
<article class="abs service" style="left:308px;top:716px"><span class="icon"></span><h3>Athletic</h3><p>There are many variations of passages of Lorem Ipsum available, but the majority variations of passages of have suffered alteration in some form</p><div class="more">Read More</div></article>

<section class="abs testimonial">
  <h3>Testrimonial</h3>
  <blockquote><b style="font-size:16px;font-style:normal">&ldquo;</b> There are many variations of passages of Lorem Ipsum available, but the majority have suffered alteration in some form, by injected humour, or randomised words which don't look even slightly believable <b style="font-size:16px;font-style:normal">&rdquo;</b></blockquote>
  <cite>maren holt<br>&nbsp;&nbsp;&nbsp;USA</cite>
  <div class="dots"><span></span><span></span><span></span><span></span></div>
</section>

<aside class="abs consult">
  <div class="consult-body"></div>
  <svg class="abs" style="left:0;top:0" width="206" height="64" viewBox="0 0 206 64"><path d="M0 0H206V34L103 58 0 34Z" fill="#474747"/></svg>
  <div class="abs condensed" style="left:0;top:2px;width:206px;text-align:center;color:#fff">
    <div style="font-size:11px;color:var(--lime)">Contact Us Now And Get Your</div>
    <div style="font-size:14px;font-weight:500;letter-spacing:1px">FREE CONSULTATION</div>
    <div style="font-size:10.5px;color:var(--lime)">— Today —</div>
  </div>
  <div class="abs condensed" style="left:0;top:64px;width:206px;text-align:center;font-size:11px;font-weight:600;color:#333">WELLNESS BEGINS HERE</div>
  <div class="field" style="top:86px">First Name</div>
  <div class="field" style="top:110px">Last Name</div>
  <div class="field" style="top:133px">Phone Number</div>
  <div class="field" style="top:157px;height:32px;padding-top:12px">Comment....</div>
  <div class="submit">SUBMIT</div>
</aside>

<aside class="abs hours">
  <h3>OFFICE HOURS</h3>
  <table>
    <tr><td style="width:62px">Monday</td><td>: 8:00-11:00, &nbsp;&nbsp;2:00-5:00</td></tr>
    <tr><td>Tuesday</td><td>: 8:30-11:00, &nbsp;&nbsp;2:00-5:30</td></tr>
    <tr><td>Wednesday</td><td>: 8:00-11:00, &nbsp;&nbsp;2:00-5:00</td></tr>
    <tr><td>Thursday</td><td>: 10:00-12:00, 2:30-5:00</td></tr>
    <tr><td>Friday</td><td>: 8:00-10:00, &nbsp;&nbsp;1:00-5:00</td></tr>
    <tr><td>Saturday</td><td>: Closed</td></tr>
    <tr><td>Sunday</td><td>: Closed</td></tr>
  </table>
</aside>

<footer class="abs site-footer">
  <div class="abs band" style="left:85px;width:325px;background:var(--orange)">BASIC INFORMATION</div>
  <div class="abs band" style="left:412px;width:325px;background:var(--cyan)">NEWS LATTERS</div>

  <div class="abs f-title" style="left:86px;top:48px">CONTACT</div>
  <div class="abs" style="left:86px;top:72px">
    <div class="f-row"><svg width="14" height="20" viewBox="0 0 14 20"><path d="M7 0A7 7 0 0 0 0 7c0 5 7 13 7 13s7-8 7-13A7 7 0 0 0 7 0z" fill="#fff"/><circle cx="7" cy="7" r="2.5" fill="#0d0d0d"/></svg><span>3168 PELHAM ORCHARD LANE, #240<br>MAPLE HOLLOW, MN 55999</span></div>
    <div class="f-row" style="margin-top:10px"><svg width="18" height="18" viewBox="0 0 18 18"><circle cx="9" cy="9" r="8" fill="none" stroke="#fff" stroke-width="1.5"/><path d="M6 5l1.6 1.6-.8 1.6c.8 1.6 1.6 2.4 3.2 3.2l1.6-.8 1.6 1.6-1.6 1.6C8 13 5 10 4.6 6.6z" fill="#fff"/></svg><span>555-314-2719</span></div>
    <div class="f-row" style="margin-top:14px"><svg width="18" height="14" viewBox="0 0 18 14"><rect x="1" y="1" width="16" height="12" fill="none" stroke="#fff" stroke-width="1.3"/><path d="M1 1l8 7 8-7" fill="none" stroke="#fff" stroke-width="1.3"/></svg><span>hello@evergreenvitality.example</span></div>
  </div>

  <div class="abs map" role="img" aria-label="Street map of the clinic's neighbourhood with a location pin"></div>

  <div class="abs f-title" style="left:512px;top:45px;font-size:11.5px">OFFICE HOURS</div>
  <table class="abs f-hours" style="left:512px;top:62px;border-collapse:collapse">
    <tr><td style="width:60px">MONDAY:</td><td>8:00-11:00, &nbsp;&nbsp;2:00-5:00</td></tr>
    <tr><td>TUESDAY:</td><td>8:30-11:00, &nbsp;&nbsp;2:00-5:30</td></tr>
    <tr><td>WEDNESDAY:</td><td>8:00-11:00, &nbsp;&nbsp;2:00-5:00</td></tr>
    <tr><td>THURSDAY :</td><td>10:00-12:00, 2:30-5:00</td></tr>
    <tr><td>FRIDAY:</td><td>8:00-10:00, &nbsp;&nbsp;1:00-5:00</td></tr>
    <tr><td>SATURDAY:</td><td>CLOSED</td></tr>
    <tr><td>SUNDAY:</td><td>CLOSED</td></tr>
  </table>
  <div class="abs powered">Powered by Brightline Site Works</div>
</footer>

</body>
</html>
```